Harbor Crestline (Business Card Design)

Need business cards designed. Something modern, chic, and sleek. Mabye the back of the card should be the navy blue that is in the logo and then just the logo on the back.

Target Market(s)

Those in the hotel, office, and renovation industry

Contact Information for Business Card

1. Logo 2. Dorian Fenwick 3. CEO/Founder 4. Phone: (833) HarbCre / (833) 427-2731 5. Email: dorian@theharborcrestline.com 6. Website: www.theharborcrestline.com

Font styles to use
Other font styles liked:
• Look at the logo font and base the font for everything else off of that.

Colors
0054AA
0677BA
7BADD7
CADEEF
E8F1F8

Requirements
Must have
• Colors that are associated in the logo
Nice to have
• Sleek modern clean and chic design.

```html
<!DOCTYPE html>
<html lang="en">
<head>
<meta charset="utf-8">
<title>Harbor Crestline — Business Card Presentation</title>
<link href="https://fonts.googleapis.com/css2?family=Montserrat:wght@300;400;500;600;700&display=swap" rel="stylesheet">
<style>
  :root {
    --board: #f3f3f3;
    --board-glow: #fbfbfb;
    --navy: #0c1940;
    --gold: #cfa449;
    --white: #ffffff;
    --ink: #1a2447;
    --label: #111111;
    --divider: #e4e4e4;
  }
  * { margin: 0; padding: 0; box-sizing: border-box; }
  html, body {
    width: 1200px; height: 941px; overflow: hidden;
    font-family: "Montserrat", Arial, sans-serif;
  }
  .board {
    position: relative; width: 1200px; height: 941px;
    background: radial-gradient(ellipse at 50% 50%, var(--board-glow) 0%, var(--board) 70%);
  }
  .row-divider {
    position: absolute; left: 0; top: 470px; width: 1200px; height: 1px;
    background: var(--divider);
  }
  .card {
    position: absolute; width: 431px; height: 247px; overflow: hidden;
    box-shadow: 0 8px 8px -6px rgba(0,0,0,0.35);
  }
  .card--front { background: var(--white); left: 86px; }
  .card--back { background: var(--navy); left: 682px; }
  .row-top .card { top: 95px; }
  .row-bottom .card { top: 565px; }
  .side-label {
    position: absolute; width: 431px; text-align: center;
    font-size: 13px; font-weight: 500; color: var(--label); letter-spacing: 0.3px;
  }
  .side-label--front { left: 86px; }
  .side-label--back { left: 682px; }
  .row-top .side-label { top: 381px; }
  .row-bottom .side-label { top: 851px; }

  .holder { position: absolute; }
  .holder-name { font-size: 12px; font-weight: 300; color: var(--ink); line-height: 1.1; }
  .holder-title { font-size: 9px; font-weight: 400; color: var(--ink); margin-top: 2px; }

  .wordmark {
    position: absolute; display: flex; align-items: center; gap: 7px;
    font-weight: 600; letter-spacing: 1.5px; white-space: nowrap;
  }
  .wordmark-square { width: 8px; height: 8px; background: var(--gold); flex: none; }
  .wordmark--front { left: 42px; top: 114px; font-size: 17px; color: var(--navy); }
  .wordmark--back {
    left: 0; right: 0; justify-content: center;
    font-size: 19px; color: var(--white);
  }
  .wordmark--back.is-centered { top: 113px; }
  .wordmark--back.is-lower { top: 158px; }

  .accent-square { position: absolute; width: 14px; height: 14px; background: var(--gold); }

  .contact { position: absolute; font-size: 9px; color: var(--ink); }
  .contact-line { display: flex; align-items: center; gap: 7px; height: 16px; }
  .contact-line svg { width: 11px; height: 11px; flex: none; }
  .contact-line strong { font-weight: 700; }
</style>
</head>
<body>
<div class="board">
  <div class="row-divider"></div>

  <section class="row-top">
    <div class="card card--front">
      <div class="holder" style="left:42px; top:41px;">
        <div class="holder-name">Dorian Fenwick</div>
        <div class="holder-title">CEO/Founder</div>
      </div>
      <div class="wordmark wordmark--front">HARBOR CRESTLINE</div>
      <div class="accent-square" style="left:362px; top:115px;"></div>
      <div class="contact" style="left:219px; top:174px;">
        <div class="contact-line">
          <svg viewBox="0 0 12 12" aria-hidden="true"><rect x="1" y="2.5" width="10" height="7" rx="1" fill="none" stroke="currentColor" stroke-width="1"/><path d="M1.3 3l4.7 3.6L10.7 3" fill="none" stroke="currentColor" stroke-width="1"/></svg>
          <span>dorian@<strong>theharborcrestline.com</strong></span>
        </div>
        <div class="contact-line">
          <svg viewBox="0 0 12 12" aria-hidden="true"><path d="M3 1.2l1.8 2.3-1 1.2c.6 1.4 1.7 2.5 3.1 3.1l1.2-1 2.3 1.8-1 1.9C5.6 10.3 1.7 6.4 1.5 2.2z" fill="currentColor"/></svg>
          <span>(833) HarbCre / (833) 427-2731</span>
        </div>
      </div>
    </div>
    <div class="card card--back">
      <div class="wordmark wordmark--back is-centered"><span class="wordmark-square"></span>HARBOR CRESTLINE</div>
    </div>
    <div class="side-label side-label--front">FRONT</div>
    <div class="side-label side-label--back">BACK</div>
  </section>

  <section class="row-bottom">
    <div class="card card--front">
      <div class="accent-square" style="left:356px; top:130px;"></div>
      <div class="holder" style="left:58px; top:124px;">
        <div class="holder-name">Dorian Fenwick</div>
        <div class="holder-title">CEO/Founder</div>
      </div>
      <div class="contact" style="left:58px; top:164px;">
        <div class="contact-line">
          <svg viewBox="0 0 12 12" aria-hidden="true"><rect x="1" y="2.5" width="10" height="7" rx="1" fill="none" stroke="currentColor" stroke-width="1"/><path d="M1.3 3l4.7 3.6L10.7 3" fill="none" stroke="currentColor" stroke-width="1"/></svg>
          <span>dorian@<strong>theharborcrestline.com</strong></span>
        </div>
        <div class="contact-line">
          <svg viewBox="0 0 12 12" aria-hidden="true"><path d="M3 1.2l1.8 2.3-1 1.2c.6 1.4 1.7 2.5 3.1 3.1l1.2-1 2.3 1.8-1 1.9C5.6 10.3 1.7 6.4 1.5 2.2z" fill="currentColor"/></svg>
          <span>(833) HarbCre / (833) 427-2731</span>
        </div>
      </div>
    </div>
    <div class="card card--back">
      <div class="accent-square" style="left:208px; top:82px;"></div>
      <div class="wordmark wordmark--back is-lower">HARBOR CRESTLINE</div>
    </div>
    <div class="side-label side-label--front">FRONT</div>
    <div class="side-label side-label--back">BACK</div>
  </section>
</div>
</body>
</html>
```